V.Lumo Gin - Bottle label Design

We are manufacturers of Gin in South Africa.
The name of our Gin is V.Lumo Gin with Q standing for Dlovikazi, a Xhosa Village in the region of Eastern Cape.

We would like our brand to depict the following (really the focus of Gold on it)
> Prosperity of the place
> Wealth of the place, land, material or in the people
> Gold rush, potential, hope

As the brand matures, we would like to have campaigns with it. See ideas below:
> V.Lumo Premium
> Crimson dusk edition
Limited edition will be released every year
- V.Lumo entabeni (location)
- V.Lumo ekhayeni (location)

> Each batch of bottles with focus on a specific area/location in Dlovikazi. One that is known and will be highlighted on the map design of the bottle.
Bottles based on landmarks in Dlovikazi and landmark design in the Big V.

Below we tried but we are not where we really want to be in terms of Gin Bottle elegance.

Target Market(s)

Target market is the young crowd. Young Xhosa men and women working really hard to get their goals. Positive thinkers. Elegant. Fresh. Bold. Age from 24 to 45. People who enjoy quality products.

Industry/Entity Type

Beverage Industry. Craft Gin.

Font styles to use
Sans Serif
Decorative

Colors
FFF300
FFF600
FEFA6F
FFFEC7
FFFEE8
FFC000
F8CF3A
FAE287
FDF2CF
FEFAEE

Requirements
Must have
• Gold colour as a theme. Try and make the background textured.

```html
<!DOCTYPE html>
<html lang="en">
<head>
<meta charset="UTF-8">
<title>V.Lumo Gin – Bottle Label</title>
<link rel="stylesheet" href="https://fonts.googleapis.com/css2?family=Montserrat:wght@300&family=Roboto+Condensed:wght@400;500&display=swap">
<style>
  :root {
    --gold-deep: #6b4508;
    --gold-mid: #a6721c;
    --gold-bright: #e6e86a;
    --gold-olive: #8a6a14;
    --gold-warm: #c9a23a;
    --panel: #e6e7e8;
    --paper: #ffffff;
    --ink: #1e1e1e;
    --band-text: #fdf2cf;
  }
  * { margin: 0; padding: 0; box-sizing: border-box; }
  html, body { width: 1200px; height: 1200px; overflow: hidden; background: var(--paper); }
  .canvas { position: relative; width: 1200px; height: 1200px; background: var(--paper); }

  .label-edge {
    position: absolute; left: 184px; top: 267px; width: 840px; height: 672px;
    background: #e3e3e3;
  }
  .label-frame {
    position: absolute; left: 187px; top: 271px; width: 833px; height: 665px;
    background: linear-gradient(90deg, var(--gold-deep) 0%, var(--gold-bright) 33%, var(--gold-warm) 50%, var(--gold-mid) 65%, var(--gold-deep) 100%);
  }
  .label-panel {
    position: absolute; left: 204px; top: 288px; width: 799px; height: 631px;
    background: var(--panel);
  }

  .landscape-art {
    position: absolute; left: 216px; top: 300px; width: 776px; height: 484px;
    background:
      radial-gradient(ellipse 55% 22% at 60% 32%, rgba(166,114,28,0.75), transparent 70%),
      radial-gradient(ellipse 45% 20% at 35% 28%, rgba(230,232,106,0.55), transparent 70%),
      linear-gradient(90deg, #ece9bf 0%, #e2dc9a 30%, #d9c99a 60%, #c9ae86 100%);
  }

  .brand-name {
    position: absolute; left: 216px; width: 776px; text-align: center;
    font-family: "Montserrat", sans-serif; font-weight: 300; color: var(--ink);
    letter-spacing: 4px;
  }
  .brand-name--main { top: 548px; font-size: 112px; line-height: 1; }
  .brand-name--sub { top: 688px; font-size: 74px; line-height: 1; }

  .facts-table {
    position: absolute; left: 215px; top: 793px; width: 778px; height: 54px;
    border-top: 3px solid var(--ink); border-bottom: 3px solid var(--ink);
    display: flex; font-family: "Roboto Condensed", sans-serif; font-weight: 500;
    font-size: 21px; color: var(--ink);
  }
  .facts-cell { display: flex; align-items: center; justify-content: center; }
  .facts-cell + .facts-cell { border-left: 3px solid var(--ink); }
  .facts-cell--origin { width: 481px; letter-spacing: 1.5px; }
  .facts-cell--volume { width: 127px; }
  .facts-cell--abv { flex: 1; }

  .botanicals-band {
    position: absolute; left: 214px; top: 856px; width: 779px; height: 51px;
    background: linear-gradient(90deg, var(--gold-deep) 0%, var(--gold-bright) 33%, var(--gold-warm) 52%, var(--gold-mid) 68%, var(--gold-deep) 100%);
    display: flex; align-items: center; justify-content: center;
    font-family: "Roboto Condensed", sans-serif; font-weight: 400; font-size: 18px;
    color: var(--band-text); letter-spacing: 0.4px;
  }
</style>
</head>
<body>
<div class="canvas">
  <div class="label-edge"></div>
  <div class="label-frame"></div>
  <div class="label-panel"></div>

  <div class="landscape-art" role="img" aria-label="Gold-foil illustration of Dlovikazi village houses beneath a hilltop, over a textured horizontal line pattern"></div>

  <div class="brand-name brand-name--main">V.LUMO</div>
  <div class="brand-name brand-name--sub">GIN</div>

  <div class="facts-table">
    <div class="facts-cell facts-cell--origin">Made in Dlovikazi vs The Eastern Cape</div>
    <div class="facts-cell facts-cell--volume">750 ml</div>
    <div class="facts-cell facts-cell--abv">43% alc.vol.</div>
  </div>

  <div class="botanicals-band">TRIPLE DISTILLED WITH JUNIPER BERRIES, CITRUS PEALS AND THE AROMAS OF DLOVIKAZI</div>
</div>
</body>
</html>
```